Nanny Share Ecommerce Website for Finding Childcare and Parents who need Childcare BrightPramHub.net

Our company needs an ecommerce website (BrightPramHub.net) for a US subscription based service strictly for nanny sharing that connects families and caregivers. The website would allow families to connect with one another as well as to search for nannies. The service would be searchable for other families by location (by radius or zip code), children demographic (age range/gender/special needs), days of week or times, after school care, school closure days (holidays), etc. The service would also be searchable for nannies based on gender, provider age range, years experience, language, hourly rate, transportation available, certification (CPR first aid), education etc. The search fields would be searchable and sortable and allow to connect with the provider (after paying subscription fee). The service would be similar to tendlyfolk.net in that it would allow for families and caregivers to post photos as well as a short bio of the themselves. There would also be a feedback/star rating mechanism to rate caregivers who have performed work for families (viewable to public). The service would be free for nannies to post their bios and only a subscription based service for families to connect with other families or with caregivers (able to view bio but need service to connect). There will be a short bio on the benefits of nanny sharing (reduced cost, increased flexibility for parents, reduced illness, increased socialization with other children vs. sole nanny), as well as Q&A section with best practices.

Target Market(s)

Families, Nannies

Industry/Entity Type

Childcare

Logo Text

Bright Pram Hub

Coding

Coded - Design and coding required

Number of Pages Required

5+ page

Requirements
Must have
• Searchable (need to be able to search for families as well as nannies), responsive, functional, easy to use, add value to families and nannies. Needs to be able to collect payment for subscription.
Nice to have
• Optimized for mobile, SEO optimized

```html
<!DOCTYPE html>
<html lang="en">
<head>
<meta charset="utf-8">
<title>Bright Pram Hub – Nanny Sharing</title>
<link href="https://fonts.googleapis.com/css2?family=Montserrat:wght@400;500;600;700&family=Open+Sans:wght@400;600;700&family=Oswald:wght@600;700&display=swap" rel="stylesheet">
<style>
:root{
  --red:#f04e51;
  --green:#7dc243;
  --dark:#262626;
  --grey:#ebebeb;
  --text:#333333;
  --muted:#555555;
  --white:#ffffff;
  --card:#eef5e6;
}
*{box-sizing:border-box;margin:0;padding:0}
html,body{width:1200px;height:3429px;overflow:hidden;background:var(--white)}
body{font-family:"Open Sans",Arial,sans-serif;color:var(--text)}
.page{position:relative;width:1200px;height:3429px;overflow:hidden}
section,header,footer{position:absolute;left:0;width:1200px}

/* Header */
.site-header{top:0;height:91px;background:var(--white);z-index:5}
.brand{position:absolute;left:100px;top:28px;display:flex;align-items:center;gap:10px;font-family:"Montserrat",sans-serif;font-weight:700;font-size:24px;color:var(--green)}
.brand-dot{width:22px;height:22px;border-radius:50%;background:var(--green)}
.main-nav{position:absolute;right:100px;top:0;height:91px;display:flex;font-family:"Montserrat",sans-serif;font-weight:600;font-size:15px}
.main-nav a{display:flex;align-items:center;padding:0 17px;color:var(--dark);text-decoration:none}
.main-nav a.active{background:var(--red);color:var(--white);padding:0 23px}

/* Hero */
.hero{top:91px;height:520px}
.hero-photo{position:absolute;inset:0;background:linear-gradient(90deg,#b8a89b 0%,#cbbdb0 35%,#e2c9b8 60%,#c99f8c 80%,#b9a496 100%)}
.hero-shade{position:absolute;inset:0;background:linear-gradient(90deg,rgba(60,45,35,.35),rgba(60,45,35,0) 55%)}
.hero-content{position:absolute;left:98px;top:76px;width:520px;color:var(--white)}
.hero-title{font-family:"Oswald",sans-serif;font-weight:700;font-size:60px;line-height:1;letter-spacing:.5px}
.hero-text{margin-top:30px;font-size:14.5px;font-weight:600;line-height:1.6}
.hero-actions{margin-top:40px;display:flex;gap:11px}
.btn{display:inline-flex;align-items:center;justify-content:center;height:50px;padding:0 20px;border:2px solid var(--white);font-family:"Montserrat",sans-serif;font-weight:700;font-size:14px;color:var(--white);text-decoration:none}
.btn-red{background:var(--red);width:119px}
.btn-green{background:var(--green);width:133px}
.slider-dots{margin-top:46px;display:flex;gap:6px}
.slider-dots span{width:16px;height:16px;border-radius:50%;background:rgba(255,255,255,.6)}
.slider-dots span:first-child{background:var(--white)}

/* Split */
.split{top:540px;height:301px;z-index:2}
.split-curve{position:absolute;top:0;left:0;width:1200px;height:70px}
.split-half{position:absolute;top:66px;height:235px;width:600px}
.split-half.care{left:0;background:var(--red)}
.split-half.job{left:600px;background:var(--green)}
.split-box{position:absolute;top:91px;width:380px;height:164px;border:2px solid rgba(255,255,255,.85);border-radius:10px;color:var(--white);text-align:center;padding:38px 34px 0}
.split-box.care{left:160px}
.split-box.job{left:663px}
.split-box h2{position:absolute;top:-15px;left:50%;transform:translateX(-50%);padding:0 12px;font-family:"Montserrat",sans-serif;font-weight:700;font-size:21px;white-space:nowrap}
.split-box.care h2{background:var(--red)}
.split-box.job h2{background:var(--green)}
.split-box p{font-size:12.5px;line-height:1.55}
.split-box .more{display:block;margin-top:24px;font-size:13px;font-weight:700}

/* Section headings */
.section-title{text-align:center;font-family:"Montserrat",sans-serif;font-weight:700;font-size:29px;color:var(--red)}
.section-rule{width:76px;height:2px;background:var(--red);margin:24px auto 0}

/* Benefits */
.benefits{top:841px;height:590px}
.benefits .section-title{margin-top:72px}
.benefit-list{position:absolute;top:194px;left:87px;display:flex}
.benefit{width:256px;text-align:center;padding:0 12px}
.benefit-icon{width:142px;height:142px;margin:0 auto;border-radius:50%;display:flex;align-items:center;justify-content:center}
.benefit.red .benefit-icon{background:var(--red)}
.benefit.green .benefit-icon{background:var(--green)}
.benefit h3{height:78px;display:flex;align-items:center;justify-content:center;margin-top:18px;font-family:"Montserrat",sans-serif;font-weight:500;font-size:19px;line-height:1.2}
.benefit.red h3{color:var(--red)}
.benefit.green h3{color:var(--green)}
.benefit p{margin-top:12px;font-size:13px;line-height:1.6;color:var(--muted)}

/* Feedback */
.feedback{top:1431px;height:537px}
.feedback-photo{position:absolute;inset:0;background:radial-gradient(ellipse at 60% 40%,#9ad167 0%,#86c94f 45%,#76bd3f 100%)}
.feedback .section-title{position:relative;color:var(--white);margin-top:58px}
.feedback .section-rule{position:relative;background:rgba(255,255,255,.8)}
.review{position:absolute;top:233px;width:433px;height:206px;background:var(--card);border:3px solid var(--red);border-radius:12px;text-align:center;padding:0 36px}
.review.one{left:131px}
.review.two{left:635px}
.avatar{position:absolute;top:-48px;left:50%;transform:translateX(-50%);width:92px;height:92px;border-radius:50%;border:4px solid var(--red);background:linear-gradient(135deg,#d8c2b0,#8a7466)}
.stars{margin-top:58px;display:flex;justify-content:center;gap:5px}
.review p{margin-top:18px;font-size:13px;font-weight:700;line-height:1.6;color:var(--dark)}
.slider-arrow{position:absolute;top:316px}
.slider-arrow.prev{left:30px}
.slider-arrow.next{right:30px}

/* Taxes */
.taxes{top:1968px;height:615px}
.taxes .section-title{margin-top:68px}
.taxes-intro{margin-top:28px;text-align:center;font-size:14.5px;font-weight:600;color:var(--dark)}
.tax-circle{position:absolute;border-radius:50%;display:flex;flex-direction:column;align-items:center;justify-content:center;text-align:center;color:var(--white);padding:0 28px}
.tax-ring{position:absolute;border-radius:50%;border:2px dashed}
.tax-circle h3{margin-top:12px;font-family:"Montserrat",sans-serif;font-weight:700;font-size:17px;line-height:1.3}
.tax-circle p{margin-top:10px;font-size:11.5px;line-height:1.55}
.tax-circle.side{width:252px;height:252px;background:var(--green);top:237px}
.tax-circle.left{left:226px}
.tax-circle.right{left:720px}
.tax-circle.center{width:274px;height:274px;top:222px;left:462px;background:var(--red);border:4px solid var(--white);z-index:2}
.tax-ring.left{left:212px;top:223px;width:280px;height:280px;border-color:var(--green)}
.tax-ring.right{left:706px;top:223px;width:280px;height:280px;border-color:var(--green)}
.tax-ring.center{left:446px;top:206px;width:306px;height:306px;border-color:var(--red);z-index:1}

/* FAQ */
.faq{top:2583px;height:420px;background:var(--grey)}
.faq .section-title{margin-top:60px}
.faq-list{position:absolute;top:170px;left:100px;width:520px;list-style:none}
.faq-item{position:relative;height:41px;width:508px;margin-bottom:15px;border:2px solid var(--dark);border-radius:21px;display:flex;align-items:center;padding-left:44px;font-size:14px;font-weight:600;color:var(--dark)}
.faq-item .toggle{position:absolute;left:5px;top:5px;width:27px;height:27px;border-radius:50%;background:var(--dark);display:flex;align-items:center;justify-content:center}
.faq-item.open{border-color:var(--red);color:var(--red);border-radius:21px 0 0 21px}
.faq-item.open .toggle{background:var(--red)}
.faq-pointer{position:absolute;right:-14px;top:-2px}
.faq-answer{position:absolute;top:166px;left:656px;width:446px;font-size:13.5px;line-height:1.6;color:var(--muted);text-align:justify}

/* Footer */
.footer-curve{position:absolute;top:2920px;left:0;width:1200px;height:90px;z-index:1}
.site-footer{top:3000px;height:429px;background:var(--dark);color:var(--white);text-align:center}
.footer-brand{margin-top:92px;display:inline-flex;align-items:center;gap:10px;font-family:"Montserrat",sans-serif;font-weight:700;font-size:26px;color:var(--white)}
.footer-brand .brand-dot{background:var(--white)}
.social{margin-top:54px;display:flex;justify-content:center;gap:9px}
.social span{width:40px;height:40px;border-radius:50%;border:2px solid var(--white)}
.footer-nav{margin-top:30px;display:flex;justify-content:center;font-family:"Montserrat",sans-serif;font-weight:600;font-size:14px}
.footer-nav a{color:var(--white);text-decoration:none;padding:0 30px;border-left:1px solid var(--white);line-height:14px}
.footer-nav a:first-child{border-left:none}
.footer-rule{width:1002px;height:1px;background:rgba(255,255,255,.7);margin:40px auto 0}
.copyright{margin-top:30px;font-size:12.5px;font-weight:600}
</style>
</head>
<body>
<div class="page">

<header class="site-header">
  <div class="brand"><span class="brand-dot"></span>Bright Pram Hub</div>
  <nav class="main-nav">
    <a class="active" href="#">HOME</a>
    <a href="#">ABOUT US</a>
    <a href="#">SERVICES</a>
    <a href="#">BENEFITS</a>
    <a href="#">FAQ</a>
    <a href="#">CONTACT US</a>
  </nav>
</header>

<section class="hero">
  <div class="hero-photo" role="img" aria-label="Photo of a smiling mother hugging her young daughter in a bright room"></div>
  <div class="hero-shade"></div>
  <div class="hero-content">
    <h1 class="hero-title">BRIGHT PRAM HUB</h1>
    <p class="hero-text">We are a US subscription based service strictly for nanny sharing that connects families and caregivers.</p>
    <div class="hero-actions">
      <a class="btn btn-red" href="#">FIND CARE</a>
      <a class="btn btn-green" href="#">FIND NANNIES</a>
    </div>
    <div class="slider-dots"><span></span><span></span><span></span><span></span><span></span></div>
  </div>
</section>

<section class="split">
  <svg class="split-curve" viewBox="0 0 1200 70" preserveAspectRatio="none">
    <path d="M0 68 C200 22 400 8 600 8 V70 H0Z" fill="var(--red)"/>
    <path d="M600 8 C820 8 1000 22 1200 40 V70 H600Z" fill="var(--green)"/>
  </svg>
  <div class="split-half care"></div>
  <div class="split-half job"></div>
  <div class="split-box care">
    <h2>I NEED A CAREGIVER</h2>
    <p>Nemo enim ipsam voluptatem quia voluptas sit aspernatur aut odit aut fugit, sed quia consequuntur magni dolores.</p>
    <a class="more">Read More &gt;&gt;</a>
  </div>
  <div class="split-box job">
    <h2>I WANT A CARE JOB</h2>
    <p>Nemo enim ipsam voluptatem quia voluptas sit aspernatur aut odit aut fugit, sed quia consequuntur magni dolores.</p>
    <a class="more">Read More &gt;&gt;</a>
  </div>
</section>

<section class="benefits">
  <h2 class="section-title">OUR BENEFITS</h2>
  <div class="section-rule"></div>
  <div class="benefit-list">
    <div class="benefit red">
      <div class="benefit-icon">
        <svg width="64" height="64" viewBox="0 0 64 64" fill="none" stroke="#fff" stroke-width="3"><rect x="6" y="16" width="46" height="28" rx="3"/><rect x="12" y="22" width="46" height="28" rx="3" fill="var(--red)"/><circle cx="35" cy="36" r="7"/></svg>
      </div>
      <h3>Reduced Cost</h3>
      <p>Nemo enim ipsam voluptatem quia voluptas sit aspernatur aut odit aut fugit, sed quia.</p>
    </div>
    <div class="benefit green">
      <div class="benefit-icon">
        <svg width="64" height="64" viewBox="0 0 64 64" fill="none" stroke="#fff" stroke-width="3"><rect x="10" y="14" width="44" height="40" rx="4"/><line x1="10" y1="26" x2="54" y2="26"/><line x1="22" y1="8" x2="22" y2="18"/><line x1="42" y1="8" x2="42" y2="18"/><polyline points="22,40 29,46 42,33"/></svg>
      </div>
      <h3>Increased<br>Flexibility For Parents</h3>
      <p>Nemo enim ipsam voluptatem quia voluptas sit aspernatur aut odit aut fugit, sed quia.</p>
    </div>
    <div class="benefit red">
      <div class="benefit-icon">
        <svg width="64" height="64" viewBox="0 0 64 64" fill="none" stroke="#fff" stroke-width="3"><path d="M32 6 L54 14 V30 C54 44 44 54 32 58 C20 54 10 44 10 30 V14Z"/><line x1="32" y1="22" x2="32" y2="42"/><line x1="22" y1="32" x2="42" y2="32"/></svg>
      </div>
      <h3>Reduced Illness</h3>
      <p>Nemo enim ipsam voluptatem quia voluptas sit aspernatur aut odit aut fugit, sed quia.</p>
    </div>
    <div class="benefit green">
      <div class="benefit-icon">
        <svg width="64" height="64" viewBox="0 0 64 64" fill="#fff"><path d="M20 10l4 9 10 1-7 7 2 10-9-5-9 5 2-10-7-7 10-1z"/><path d="M44 22l3 7 8 1-6 5 2 8-7-4-7 4 2-8-6-5 8-1z"/><rect x="8" y="48" width="48" height="4" rx="2"/></svg>
      </div>
      <h3>Increased Socialization With Other Children vs. Sole Nanny</h3>
      <p>Nemo enim ipsam voluptatem quia voluptas sit aspernatur aut odit aut fugit, sed quia.</p>
    </div>
  </div>
</section>

<section class="feedback">
  <div class="feedback-photo" role="img" aria-label="Soft green-toned photo of a family outdoors"></div>
  <h2 class="section-title">OUR FEEDBACK</h2>
  <div class="section-rule"></div>
  <svg class="slider-arrow prev" width="24" height="60" viewBox="0 0 24 60" fill="none" stroke="#fff" stroke-width="2"><polyline points="22,2 2,30 22,58"/></svg>
  <div class="review one">
    <div class="avatar" role="img" aria-label="Portrait of a reviewing parent"></div>
    <div class="stars">
      <svg width="110" height="18" viewBox="0 0 110 18"><g fill="var(--red)"><path id="st" d="M9 1l2.4 5.2 5.6.6-4.2 3.8 1.2 5.6L9 13.4 4 16.2l1.2-5.6L1 6.8l5.6-.6z"/><use href="#st" x="23"/><use href="#st" x="46"/><use href="#st" x="69"/></g><use href="#st" x="92" fill="none" stroke="var(--red)" stroke-width="1.4"/></svg>
    </div>
    <p>Nemo enim ipsam voluptatem quia voluptas sit aspernatur aut odit aut fugit, sed quia consequuntur magni dolores eos qui ratione.</p>
  </div>
  <div class="review two">
    <div class="avatar" role="img" aria-label="Portrait of a reviewing parent"></div>
    <div class="stars">
      <svg width="110" height="18" viewBox="0 0 110 18"><g fill="var(--red)"><use href="#st"/><use href="#st" x="23"/><use href="#st" x="46"/><use href="#st" x="69"/></g><use href="#st" x="92" fill="none" stroke="var(--red)" stroke-width="1.4"/></svg>
    </div>
    <p>Nemo enim ipsam voluptatem quia voluptas sit aspernatur aut odit aut fugit, sed quia consequuntur magni dolores eos qui ratione.</p>
  </div>
  <svg class="slider-arrow next" width="24" height="60" viewBox="0 0 24 60" fill="none" stroke="#fff" stroke-width="2"><polyline points="2,2 22,30 2,58"/></svg>
</section>

<section class="taxes">
  <h2 class="section-title">NANNY TAXES MADE EASY</h2>
  <div class="section-rule"></div>
  <p class="taxes-intro">Our experts can handle all of your household employment obligations–from payroll to tax time.</p>
  <div class="tax-ring left"></div>
  <div class="tax-ring right"></div>
  <div class="tax-ring center"></div>
  <div class="tax-circle side left">
    <svg width="40" height="36" viewBox="0 0 40 36" fill="none" stroke="#fff" stroke-width="2.5"><path d="M20 6 C14 2 6 2 2 4 V32 C6 30 14 30 20 34 C26 30 34 30 38 32 V4 C34 2 26 2 20 6Z"/><line x1="20" y1="6" x2="20" y2="34"/></svg>
    <h3>ENJOY CONCIERGE<br>SUPPORT</h3>
    <p>Nemo enim ipsam voluptatem quia voluptas sit aspernatur aut odit aut fugit, sed</p>
  </div>
  <div class="tax-circle center">
    <svg width="44" height="44" viewBox="0 0 44 44" fill="none" stroke="#fff" stroke-width="2.5"><circle cx="22" cy="24" r="17"/><polyline points="22,14 22,24 29,28"/><line x1="17" y1="3" x2="27" y2="3"/></svg>
    <h3>SAVE TIME AND<br>STRESS</h3>
    <p>Nemo enim ipsam voluptatem quia voluptas sit aspernatur aut odit aut fugit, sed</p>
  </div>
  <div class="tax-circle side right">
    <svg width="40" height="40" viewBox="0 0 40 40" fill="none" stroke="#fff" stroke-width="2.5"><path d="M20 4 L34 10 V20 C34 29 28 35 20 38 C12 35 6 29 6 20 V10Z"/><polyline points="13,20 18,25 28,15"/></svg>
    <h3>GAIN UNPARALLELED<br>EXPERTISE</h3>
    <p>Nemo enim ipsam voluptatem quia voluptas sit aspernatur aut odit aut fugit, sed</p>
  </div>
</section>

<section class="faq">
  <h2 class="section-title">OUR FAQ</h2>
  <ul class="faq-list">
    <li class="faq-item open">
      <span class="toggle"><svg width="13" height="13" viewBox="0 0 13 13" stroke="#fff" stroke-width="2.5"><line x1="6.5" y1="1" x2="6.5" y2="12"/><line x1="1" y1="6.5" x2="12" y2="6.5"/></svg></span>
      Nemo enim ipsam voluptatem quia voluptas
      <svg class="faq-pointer" width="18" height="41" viewBox="0 0 18 41" fill="var(--grey)" stroke="var(--red)" stroke-width="2"><polyline points="0,1 16,20.5 0,40"/></svg>
    </li>
    <li class="faq-item">
      <span class="toggle"><svg width="13" height="13" viewBox="0 0 13 13" stroke="#fff" stroke-width="2.5"><line x1="1" y1="6.5" x2="12" y2="6.5"/></svg></span>
      Sed ut perspiciatis unde omnis iste natus error sit
    </li>
    <li class="faq-item">
      <span class="toggle"><svg width="13" height="13" viewBox="0 0 13 13" stroke="#fff" stroke-width="2.5"><line x1="1" y1="6.5" x2="12" y2="6.5"/></svg></span>
      Neque porro quisquam est, qui dolorem ipsum quia
    </li>
  </ul>
  <p class="faq-answer">Sed ut perspiciatis unde omnis iste natus error sit voluptatem accusantium doloremque laudantium, totam rem aperiam, eaque ipsa quae ab illo inventore veritatis et quasi architecto beatae vitae dicta sunt explicabo.</p>
</section>

<svg class="footer-curve" viewBox="0 0 1200 90" preserveAspectRatio="none">
  <path d="M0 20 Q600 130 1200 20 V90 H0Z" fill="var(--dark)"/>
</svg>

<footer class="site-footer">
  <div class="footer-brand"><span class="brand-dot"></span>Bright Pram Hub</div>
  <div class="social"><span></span><span></span><span></span><span></span><span></span></div>
  <nav class="footer-nav">
    <a href="#">Home</a><a href="#">About Us</a><a href="#">Services</a><a href="#">Benefits</a><a href="#">FAQ</a><a href="#">Contact Us</a>
  </nav>
  <div class="footer-rule"></div>
  <p class="copyright">Copyright © 2018 Bright Pram Hub. All Right Reserved</p>
</footer>

</div>
</body>
</html>
```